Social Media Graphics - Oakline Push REVISED

Create 6-7 individual social media graphics (square size) to encourage folks to join our online course called:

The Harvest Ledger Circle
How to Launch a Multi-Million Business From Scratch
Sign Up Today!

IMPORTANT: Make the largest and most prominent text on the graphic be: How to Launch a Multi-Million Business From Scratch

For the color scheme of the graphics, let's try a blue color palette; make sure the graphics appeal to both men and women

Make sure each graphic contains 1 of the 3 pics attached (crop pic as needed); and make sure one of the graphics is all TEXT only.

Target Market(s)

men and women looking to start a business

Industry/Entity Type

Entrepreneurship

Colors
0054AA
0677BA
7BADD7
CADEEF
E8F1F8

Requirements
Must have
• All the text and use the 3 pics provided; one graphic can be all text; Simple, modern design that's easy to read

```html
<!DOCTYPE html>
<html lang="en">
<head>
<meta charset="utf-8">
<title>The Harvest Ledger Circle – Sign Up Today</title>
<link rel="stylesheet" href="https://fonts.googleapis.com/css2?family=Bebas+Neue&display=swap">
<style>
  :root {
    --sky: #0a93d4;
    --ocean: #0063a8;
    --deep: #003f70;
    --navy: #1f2040;
    --stone: #b3aaa6;
    --white: #ffffff;
    --photo-warm: #6b4a3a;
    --photo-suit-blue: #2b4f8a;
    --photo-suit-grey: #a49c96;
  }
  * { margin: 0; padding: 0; box-sizing: border-box; }
  html, body { width: 1200px; height: 1200px; overflow: hidden; }
  body { font-family: "Bebas Neue", "Arial Narrow", sans-serif; color: var(--white); }

  .poster {
    position: relative;
    width: 1200px;
    height: 1200px;
    overflow: hidden;
    background: radial-gradient(ellipse 75% 60% at 45% 4%, var(--sky) 0%, var(--ocean) 45%, var(--deep) 100%);
  }

  .host-photo {
    position: absolute;
    border-radius: 40% 40% 6px 6px / 30% 30% 6px 6px;
  }
  .host-photo--left {
    left: 87px; top: 112px; width: 320px; height: 508px;
    background: linear-gradient(180deg, var(--photo-warm) 0%, var(--photo-suit-blue) 55%, #324f86 100%);
  }
  .host-photo--right {
    left: 660px; top: 112px; width: 452px; height: 475px;
    background: linear-gradient(180deg, var(--photo-warm) 0%, var(--photo-suit-grey) 45%, #8f8782 100%);
  }

  .course-title {
    position: absolute;
    left: 412px; top: 190px; width: 243px;
    text-align: center;
    font-size: 72px;
    line-height: 76px;
    letter-spacing: 1px;
    font-weight: 400;
    z-index: 2;
  }

  .title-plate {
    position: absolute;
    left: 87px; top: 615px; width: 1018px; height: 150px;
    z-index: 3;
  }
  .title-plate__shadow {
    position: absolute;
    left: 8px; top: -15px; width: 1026px; height: 150px;
    background: var(--stone);
    border-radius: 22px;
  }
  .title-plate__face {
    position: absolute;
    inset: 0;
    background: var(--navy);
    border-radius: 22px;
    display: flex; align-items: center; justify-content: center;
    font-size: 78px;
    letter-spacing: 30px;
    padding: 8px 0 0 30px;
  }

  .headline {
    position: absolute;
    left: 0; top: 800px; width: 1200px;
    text-align: center;
    font-size: 88px;
    line-height: 94px;
    letter-spacing: 1px;
    font-weight: 400;
  }

  .cta-divider {
    position: absolute;
    left: 160px; top: 1010px; width: 902px; height: 30px;
    display: flex; align-items: center; gap: 22px;
    font-size: 28px; letter-spacing: 12px;
  }
  .cta-divider__rule { flex: 1; height: 1.5px; background: var(--white); }

  .signup-button {
    position: absolute;
    left: 440px; top: 1064px; width: 352px; height: 40px;
    background: var(--navy);
    display: flex; align-items: center; justify-content: center;
    font-size: 28px; letter-spacing: 13px;
    padding: 3px 0 0 13px;
  }
</style>
</head>
<body>
  <main class="poster">
    <div class="host-photo host-photo--left" role="img" aria-label="Photo of a smiling female course host in a blue blazer, leaning on the title plate"></div>
    <div class="host-photo host-photo--right" role="img" aria-label="Photo of a smiling male course host in a grey blazer speaking into a microphone"></div>

    <h1 class="course-title">The<br>Harvest<br>Ledger</h1>

    <div class="title-plate">
      <div class="title-plate__shadow"></div>
      <div class="title-plate__face">Circle</div>
    </div>

    <h2 class="headline">How to launch a multi-million<br>business from scratch</h2>

    <div class="cta-divider">
      <span class="cta-divider__rule"></span>
      <span>CTA</span>
      <span class="cta-divider__rule"></span>
    </div>

    <div class="signup-button">Sign up today</div>
  </main>
</body>
</html>
```